Home Loan Introducer needs logo/business cards

We need a simple but classy logo for business cards and flyers. The business is a home loan referral business that is called an Introducer. The business name is "The Harborline".
I was thinking very simple and straight to the point on the front with "Home Loans" the only thing on the front with a nice background colour/s.
Then on the back, "The Harborline"
and "Quality Customer Service"
and "Email, text or call welcome"
and then my name, email address and phone number.
Updates
Thank you for all the designs :-)
Target Market(s)
Home buyers.
Home owners.
Investors.
Industry/Entity Type
Loan
Look and feel

```html
<!DOCTYPE html>
<html lang="en">
<head>
<meta charset="utf-8">
<title>The Harborline — Business Cards</title>
<link href="https://fonts.googleapis.com/css2?family=Exo+2:wght@400;500;600;800&display=swap" rel="stylesheet">
<style>
  :root {
    --page: #e9e4dd;
    --charcoal: #1e1e1e;
    --orange: #f7ad38;
    --orange-soft: #fbd9a3;
    --blue: #1466c0;
    --white: #ffffff;
    --ink: #161616;
  }
  * { margin: 0; padding: 0; box-sizing: border-box; }
  html, body {
    width: 1200px; height: 750px; overflow: hidden;
    background: var(--page);
    font-family: "Exo 2", sans-serif;
  }
  .canvas { position: relative; width: 1200px; height: 750px; }

  .card {
    position: absolute;
    width: 500px; height: 300px;
    background: var(--charcoal);
    overflow: hidden;
    box-shadow: 0 10px 24px rgba(0,0,0,.25);
  }

  /* Details side */
  .card--details { left: 170px; top: 80px; }
  .card--details .lower-band {
    position: absolute; inset: 0;
    background: var(--orange);
    clip-path: polygon(0 67%, 100% 56%, 100% 100%, 0 100%);
  }
  .card--details .house-art {
    position: absolute; left: 40px; top: 206px; width: 190px; height: 94px;
    background: linear-gradient(180deg, var(--orange-soft), #fcdcaa);
    border-radius: 4px 4px 0 0;
  }
  .brand {
    position: absolute; left: 0; top: 66px; width: 300px;
    display: flex; align-items: center; justify-content: center; gap: 10px;
  }
  .brand__dot { width: 16px; height: 16px; border-radius: 50%; background: var(--orange); }
  .brand__name {
    color: var(--white); font-weight: 600; font-size: 24px; letter-spacing: .5px;
    text-transform: uppercase;
  }
  .perks {
    position: absolute; right: 18px; top: 118px; list-style: none;
    color: var(--blue); font-size: 14px; font-weight: 500; line-height: 19px;
  }
  .perks li { display: flex; align-items: center; gap: 5px; }
  .perks svg { width: 12px; height: 12px; flex: none; }
  .contact {
    position: absolute; right: 22px; top: 188px; width: 170px; text-align: center;
  }
  .contact__name {
    color: var(--ink); font-size: 19px; font-weight: 500;
    padding-bottom: 4px; border-bottom: 1.5px solid var(--white);
  }
  .contact__lines { margin-top: 4px; font-size: 9.5px; line-height: 12px; color: var(--ink); }
  .contact__lines span { color: var(--blue); }

  /* Front side */
  .card--front { left: 530px; top: 360px; }
  .card--front .title-band {
    position: absolute; left: 0; right: 0; top: 108px; height: 96px;
    background: var(--orange);
    border-top: 4px solid var(--white);
    border-bottom: 4px solid var(--white);
    display: flex; align-items: center; justify-content: center; gap: 18px;
  }
  .title-band .word { font-size: 56px; font-weight: 800; letter-spacing: 1px; line-height: 1; }
  .word--home { color: var(--white); }
  .word--loan { color: var(--blue); }
</style>
</head>
<body>
<main class="canvas">

  <section class="card card--details" aria-label="Business card, details side">
    <div class="lower-band"></div>
    <div class="house-art" role="img" aria-label="Large pale house illustration"></div>
    <div class="brand">
      <span class="brand__dot"></span>
      <span class="brand__name">The Harborline</span>
    </div>
    <ul class="perks">
      <li><svg viewBox="0 0 12 12"><path d="M1 6.5 L4.5 10 L11 1.5" fill="none" stroke="#ffffff" stroke-width="2"/></svg>Quality Customer Service</li>
      <li><svg viewBox="0 0 12 12"><path d="M1 6.5 L4.5 10 L11 1.5" fill="none" stroke="#ffffff" stroke-width="2"/></svg>Email, text or call welcome</li>
    </ul>
    <div class="contact">
      <p class="contact__name">Dale Morrow</p>
      <p class="contact__lines">Phone: <span>+630955147</span><br>Email: <span>Mail@harborline.net</span></p>
    </div>
  </section>

  <section class="card card--front" aria-label="Business card, front side">
    <div class="title-band">
      <span class="word word--home">HOME</span>
      <span class="word word--loan">LOAN</span>
    </div>
  </section>

</main>
</body>
</html>
```